HearthMile business card and stationary design

We are looking for a simple yet elegant design for our mortgage company business card and stationary.

The card should include:
Name (Marcus Pell)
Title (CEO)
Phone Number (541-555-0182)
Address (48 Birchwell Court, Suite 314, Larkfield, OR 97455)
Email (email@hearthmile.example)
"NMLS" i.e. (NMLS 61947)
"Company NMLS" (Company NMLS 274615)

Contact Information for Business Card

See above

```html
<!DOCTYPE html>
<html lang="en">
<head>
<meta charset="utf-8">
<title>HearthMile Business Card</title>
<link href="https://fonts.googleapis.com/css2?family=Montserrat:wght@600&family=Arimo:wght@400;700&display=swap" rel="stylesheet">
<style>
  :root {
    --navy: #1a2533;
    --blue: #29a3e0;
    --white: #ffffff;
    --backdrop: #c9c9c9;
    --text-light: #e8edf2;
  }
  * { margin: 0; padding: 0; box-sizing: border-box; }
  html, body {
    width: 1200px;
    height: 788px;
    overflow: hidden;
    background: var(--backdrop);
    font-family: "Arimo", Arial, sans-serif;
  }
  .stage { position: relative; width: 1200px; height: 788px; }
  .card {
    position: absolute;
    width: 520px;
    height: 300px;
    border-radius: 22px;
    overflow: hidden;
    box-shadow: 0 14px 30px rgba(0,0,0,0.25);
  }
  .card-front { left: 50px; top: 90px; background: var(--white); }
  .card-back  { left: 630px; top: 400px; background: var(--navy); }
  .front-shapes { position: absolute; inset: 0; }
  .wordmark {
    position: absolute;
    font-family: "Montserrat", Arial, sans-serif;
    font-weight: 600;
    letter-spacing: 0.5px;
    white-space: nowrap;
  }
  .card-front .wordmark { left: 30px; top: 60px; font-size: 38px; line-height: 44px; color: var(--navy); }
  .card-back .wordmark {
    left: 0; right: 0; top: 112px;
    text-align: center; font-size: 58px; color: var(--white);
  }
  .contact {
    position: absolute;
    right: 26px; top: 92px;
    text-align: right;
    color: var(--text-light);
    font-size: 11px;
    line-height: 17px;
  }
  .contact .person-name {
    color: var(--blue);
    font-weight: 700;
    font-size: 19px;
    letter-spacing: 0.5px;
    line-height: 20px;
  }
  .contact .person-title { font-size: 11px; margin-right: 2px; }
  .contact .rule {
    width: 28px; height: 1px; background: var(--blue);
    margin: 4px 0 4px auto;
  }
  .contact-line { display: flex; justify-content: flex-end; align-items: center; gap: 6px; }
  .contact-line svg { width: 10px; height: 10px; flex: none; }
  .icon-gap { width: 10px; flex: none; }
  .address {
    position: absolute;
    left: 30px; bottom: 22px;
    color: var(--text-light);
    font-size: 12px;
    line-height: 16px;
  }
  .address .company-nmls { color: var(--blue); }
</style>
</head>
<body>
<main class="stage">
  <section class="card card-front" aria-label="Business card front">
    <svg class="front-shapes" viewBox="0 0 520 300" width="520" height="300" aria-hidden="true">
      <polygon points="0,240 360,70 520,35 520,300 0,300" fill="var(--navy)"/>
      <polygon points="240,124 358,63 520,26 520,32 360,70 250,122" fill="var(--blue)"/>
    </svg>
    <div class="wordmark">HearthMile</div>
    <div class="contact">
      <div class="person-name">MARCUS PELL</div>
      <div class="person-title">CEO</div>
      <div class="rule"></div>
      <div class="contact-line"><span>NMLS 61947</span><span class="icon-gap"></span></div>
      <div class="contact-line"><span>541-555-0182</span>
        <svg viewBox="0 0 10 10"><path d="M2 1 L4 1 L4.6 3 L3.4 3.8 Q4.4 5.8 6.2 6.6 L7 5.4 L9 6 L9 8 Q8 9 6.5 8.8 Q2.2 7.6 1.2 3.4 Q1 2 2 1Z" fill="var(--blue)"/></svg>
      </div>
      <div class="contact-line"><span>email@hearthmile.example</span>
        <svg viewBox="0 0 10 10"><rect x="0.5" y="2" width="9" height="6.5" rx="1" fill="var(--blue)"/><path d="M1 2.6 L5 5.6 L9 2.6" stroke="var(--navy)" stroke-width="0.9" fill="none"/></svg>
      </div>
      <div class="contact-line"><span>www.hearthmile.example</span>
        <svg viewBox="0 0 10 10"><circle cx="5" cy="5" r="4.4" fill="var(--blue)"/><path d="M0.8 5 H9.2 M5 0.6 Q2.4 5 5 9.4 M5 0.6 Q7.6 5 5 9.4" stroke="var(--navy)" stroke-width="0.7" fill="none"/></svg>
      </div>
    </div>
    <div class="address">
      <div>48 Birchwell Court, Suite</div>
      <div>314, Larkfield, OR 97455</div>
      <div class="company-nmls">Company NMLS 274615</div>
    </div>
  </section>

  <section class="card card-back" aria-label="Business card back">
    <div class="wordmark">HearthMile</div>
  </section>
</main>
</body>
</html>
```